Varnik Holdings — Business Card Design Brief
Overview
Design a double-sided business card for Varnik Holdings that highlights our two service arms: Varnik Communications (telecommunications) and Varnik Energy (business energy solutions). The card should feel smart and stand out when handed to clients.

Objectives
Showcase our areas of specialty clearly.
Reflect the overall Varnik / Varnik Holdings brand while acknowledging both arms.
Explore using both logos (Communications + Energy) or one unified logo, depending on the design.

Deliverables
One double-sided business card design (front + back).

Content & Copy
Front (preferred): Logo: Varnik / Varnik Holdings
Descriptor: Business Communications | Business Energy
Back:My contact details and company details
Core products: Business Mobile • Telephony • Internet • Business Energy Solutions

Brand & Visual Direction
We have a group logo currently tailored more toward telecoms, plus a separate Varnik Energy logo.
Please explore layouts that use both logos or just one, whichever works best.
Color: I wouldn't mind seeing an option using our the Blue/Purple gradient from our website (varnik-example.co.uk), but also open to non-gradient approaches and other colours..

Overall look: Smart, modern, and distinctive.
Format & Print Specs
Double-sided business card format. (Use a standard size

Must-Haves
Front: Varnik wording or Varnik Holdings wording with atleast 1 logo also on front “Business Communications | Business Energy.”

Back: Contact + company details and core products.
A design that stands out while remaining professional.

Nice-to-Have Options
A gradient version using our site’s Blue/Purple gradient.
A non-gradient version.
A dual-logo treatment versus a single-logo treatment.

Thanks
Owen

```html
<!DOCTYPE html>
<html lang="en">
<head>
<meta charset="utf-8">
<title>Varnik Holdings — Business Card</title>
<link href="https://fonts.googleapis.com/css2?family=Roboto:wght@400;500;700;900&display=swap" rel="stylesheet">
<style>
  :root {
    --bg: #e6e6e6;
    --paper: #ffffff;
    --navy: #1b1464;
    --stripe: #1f7be0;
    --stripe-light: #29a9e1;
    --green: #5bb21e;
    --lime: #a8c81a;
    --blue: #1a6fd6;
    --sky: #1e9fe0;
    --text-light: #ffffff;
    --rule: #8a8a8a;
  }
  * { box-sizing: border-box; margin: 0; padding: 0; }
  html, body { width: 1200px; height: 1200px; overflow: hidden; }
  body {
    background: var(--bg);
    font-family: "Roboto", Arial, sans-serif;
    position: relative;
  }
  .card {
    position: absolute;
    left: 255px;
    width: 690px;
    height: 394px;
    background: var(--paper);
    overflow: hidden;
  }
  .card--front { top: 160px; }
  .card--back { top: 652px; display: flex; align-items: center; justify-content: center; }

  /* front top */
  .brand-row {
    height: 214px;
    display: flex;
    align-items: center;
    justify-content: center;
    padding-top: 20px;
  }
  .brand {
    display: flex;
    align-items: center;
    gap: 14px;
    width: 260px;
    justify-content: center;
  }
  .brand__dot { width: 40px; height: 40px; border-radius: 50%; flex: none; }
  .brand__dot--energy { background: var(--green); }
  .brand__dot--comms { background: var(--blue); }
  .brand__name {
    font-weight: 900;
    font-size: 46px;
    letter-spacing: 1px;
    color: var(--navy);
  }
  .brand-divider { width: 1px; height: 150px; background: var(--rule); margin: 0 10px; }

  .stripe {
    height: 8px;
    background: linear-gradient(90deg, var(--stripe), var(--stripe-light));
    border-bottom: 2px solid var(--paper);
  }
  .details {
    height: 172px;
    background: var(--navy);
    color: var(--text-light);
    padding-top: 26px;
    text-align: center;
  }
  .person { display: flex; align-items: baseline; justify-content: center; gap: 8px; }
  .person__name { font-weight: 700; font-size: 27px; color: var(--lime); letter-spacing: .5px; }
  .person__slash { font-size: 26px; color: var(--lime); }
  .person__role { font-size: 15px; color: var(--sky); }

  .contacts {
    display: flex;
    justify-content: center;
    align-items: center;
    margin-top: 12px;
    font-size: 16px;
    line-height: 21px;
  }
  .contacts__col { text-align: left; padding: 0 20px; }
  .contacts__col + .contacts__col { border-left: 1.5px solid var(--text-light); }
  .contacts__col:first-child { padding-left: 0; }
  .contacts__line { display: flex; align-items: center; gap: 10px; }
  .contacts__line svg { width: 14px; height: 14px; flex: none; }

  .products {
    margin-top: 16px;
    font-size: 17px;
  }
  .products .sep { color: var(--sky); margin: 0 6px; }

  /* back */
  .arm {
    width: 290px;
    display: flex;
    flex-direction: column;
    align-items: center;
    gap: 24px;
  }
  .arm__label { font-size: 16px; letter-spacing: .2px; }
  .arm--comms .arm__label { color: var(--sky); }
  .arm--energy .arm__label { color: var(--lime); }
  .arm-divider { width: 1px; height: 150px; background: var(--rule); margin: 0 14px; }
</style>
</head>
<body>

<section class="card card--front">
  <div class="brand-row">
    <div class="brand">
      <span class="brand__dot brand__dot--energy"></span>
      <span class="brand__name">VARNIK</span>
    </div>
    <div class="brand-divider"></div>
    <div class="brand">
      <span class="brand__dot brand__dot--comms"></span>
      <span class="brand__name">VARNIK</span>
    </div>
  </div>
  <div class="stripe"></div>
  <div class="details">
    <div class="person">
      <span class="person__name">DANIEL MORROW</span>
      <span class="person__slash">/</span>
      <span class="person__role">President</span>
    </div>
    <div class="contacts">
      <div class="contacts__col">
        <div>4120 Alder Crescent</div>
        <div>Kelston, Canada 58213</div>
      </div>
      <div class="contacts__col">
        <div class="contacts__line">
          <svg viewBox="0 0 16 16"><path fill="#a8c81a" d="M3.5 1.5l2.5 0 1 3.5-1.6 1.2a9 9 0 0 0 4.4 4.4l1.2-1.6 3.5 1v2.5c0 .8-.7 1.5-1.5 1.5A12.5 12.5 0 0 1 2 3c0-.8.7-1.5 1.5-1.5z"/></svg>
          <span>555-218-4096</span>
        </div>
        <div class="contacts__line">
          <svg viewBox="0 0 16 16"><rect x="3.5" y="1" width="9" height="14" rx="1.5" fill="none" stroke="#a8c81a" stroke-width="1.6"/><circle cx="8" cy="12.5" r=".9" fill="#a8c81a"/></svg>
          <span>555-374-1182</span>
        </div>
      </div>
      <div class="contacts__col">
        <div class="contacts__line">
          <svg viewBox="0 0 16 16"><rect x="1.5" y="3.5" width="13" height="9" fill="none" stroke="#5bb21e" stroke-width="1.6"/><path d="M1.5 3.5l6.5 5 6.5-5" fill="none" stroke="#5bb21e" stroke-width="1.6"/></svg>
          <span>info@VARNIK-EXAMPLE.com</span>
        </div>
        <div class="contacts__line">
          <svg viewBox="0 0 16 16"><circle cx="8" cy="8" r="6.5" fill="none" stroke="#5bb21e" stroke-width="1.6"/><path d="M1.5 8h13M8 1.5c-2.5 3-2.5 10 0 13M8 1.5c2.5 3 2.5 10 0 13" fill="none" stroke="#5bb21e" stroke-width="1.2"/></svg>
          <span>www.VARNIK-EXAMPLE.com</span>
        </div>
      </div>
    </div>
    <p class="products">Business Mobile<span class="sep">•</span>Telephony<span class="sep">•</span>Internet<span class="sep">•</span>Business Energy Solutions</p>
  </div>
</section>

<section class="card card--back">
  <div class="arm arm--comms">
    <div class="brand">
      <span class="brand__dot brand__dot--comms"></span>
      <span class="brand__name">VARNIK</span>
    </div>
    <span class="arm__label">BUSINESS COMMUNICATIONS</span>
  </div>
  <div class="arm-divider"></div>
  <div class="arm arm--energy">
    <div class="brand">
      <span class="brand__dot brand__dot--energy"></span>
      <span class="brand__name">VARNIK</span>
    </div>
    <span class="arm__label">BUSINESS ENERGY</span>
  </div>
</section>

</body>
</html>
```